A modern and fresh looking church website

Elmridge is looking for a new site design for their church. The church is a part of a group of the ‘Covenant Fellowship’ Australia and needs to kind of tie into their branding within reason.
This means, we would need to use the logo colours (Blue, Gold, Red) throughout the website and the design needs to be fresh, modern, clean, and mobile-friendly. The front page must have the following as features:
• Sermons (Podcasts and Videos)
• Events
• Venue Hire (Weddings)
The website will be mainly information-based and will have a few forms. From our recent engagement with the church, I did draft up a mock-up design for them and even it looks better than their current site, it’s not giving a ‘stand out impression’ and has that out of date look.
The inner pages will be based off the front-page design so we will take care of that, we are just looking for a front-page design that is unique and has the wow factor.
The website will be coded by our in-house development team and will be coded in a WordPress format using Elementor pro.
We are looking for a couple of designers to design 1-3 mock-ups by taking our current draft and putting their spin to it.
Updates
Hi,
Due to Christmas and the client was on leave, the design selection has been delayed. It was not ideal as I knew this would happen.
I made contact with the client and just been told that the client is leaving the church and a handover is happening for the new staff member. The new staff member will present all designs to the board for selection. This is due to be completed by the first week of February 2021.
We thanks for your patients as this was not expected and we seeing if we can hurry this process up.

```html
<!DOCTYPE html>
<html lang="en">
<head>
<meta charset="utf-8">
<title>Elmridge Covenant Fellowship — Home</title>
<link rel="stylesheet" href="https://fonts.googleapis.com/css2?family=Montserrat:wght@400;500;600&family=Roboto:wght@400;700&family=Tinos:ital,wght@0,400;0,700;1,400&display=swap">
<style>
:root{
  --navy:#153e66;
  --navy-dark:#0f2f50;
  --blue:#0c5aa6;
  --red:#c8242b;
  --gold:#a07c2c;
  --panel:#f2f2f2;
  --panel-line:#d4d4d4;
  --ink:#222;
  --muted:#8a8a8a;
  --backdrop:#f4f4f4;
  --white:#fff;
}
*{box-sizing:border-box;margin:0;padding:0}
html,body{width:1200px;height:2400px;overflow:hidden;background:var(--backdrop)}
body{font-family:'Montserrat',sans-serif;color:var(--ink);position:relative}
.page{position:absolute;left:90px;top:37px;width:1019px;height:2325px;background:var(--white);box-shadow:0 10px 40px rgba(0,0,0,.25);overflow:hidden}
.abs{position:absolute}

/* header */
.topbar{left:0;top:0;width:1019px;height:51px;background:var(--navy)}
.social{top:9px;width:18px;height:18px;border:1.5px solid #fff;border-radius:50%}
.social svg{position:absolute;left:3px;top:3px}
.contact-btn{left:798px;top:11px;width:69px;height:16px;border:1px solid #fff;color:#fff;font-size:9px;letter-spacing:1.5px;text-align:center;line-height:14px}
.hero{left:0;top:51px;width:1019px;height:534px;background:linear-gradient(180deg,#5d5a58 0%,#4a4642 45%,#3b3733 100%)}
.hero-shade{left:0;top:51px;width:1019px;height:534px;background:radial-gradient(ellipse at 50% 60%,rgba(150,120,100,.35),rgba(0,0,0,.15) 70%)}
.nav{left:174px;top:35px;width:693px;height:28px;background:#fff;font-size:9px;letter-spacing:.6px;color:#444}
.nav span{position:absolute;top:9px;white-space:nowrap}
.nav .active{font-weight:600;color:#111}
.nav .sep{width:1px;height:12px;background:#bbb;top:8px}
.logo-tab{left:465px;top:9px;width:116px;height:122px}
.logo-name{left:465px;top:62px;width:116px;text-align:center;color:var(--navy);font-weight:600;font-size:17px;letter-spacing:.5px}
.logo-sub{left:465px;top:84px;width:116px;text-align:center;color:var(--navy);font-size:6px;letter-spacing:.3px}
.logo-top{left:465px;top:23px;width:116px;text-align:center;color:var(--navy);font-size:8px;font-weight:600;line-height:10px}
.quote{left:0;top:163px;width:1019px;text-align:center;font-family:'Tinos',serif;font-style:italic;color:#fff;font-size:28px;line-height:34px}
.schedule-btn{left:436px;top:281px;width:172px;height:32px;background:rgba(35,35,35,.85);color:#fff;font-size:16px;letter-spacing:3px;text-align:center;line-height:32px}
.band{left:0;top:584px;width:1019px;height:100px;background:var(--navy);color:#fff;text-align:center;font-family:'Roboto',sans-serif}
.band-title{position:absolute;left:0;width:100%;top:13px;font-size:22px;letter-spacing:1px}
.band-times{position:absolute;left:0;width:100%;top:45px;font-size:35px;font-weight:700}

/* feature cards */
.card{top:729px;width:183px;height:252px}
.card-body{position:absolute;left:0;top:23px;width:183px;height:229px;background:#fff;box-shadow:0 1px 5px rgba(0,0,0,.35)}
.card-arch{position:absolute;left:47px;top:0;width:89px;height:40px;border-radius:45px 45px 0 0}
.card-head{position:absolute;left:0;top:0;width:183px;height:55px;color:#fff;font-family:'Tinos',serif;font-size:22px;letter-spacing:1px;text-align:center;line-height:55px}
.card-photo{position:absolute;left:0;top:55px;width:183px;height:85px}
.card-text{position:absolute;left:12px;top:148px;width:159px;font-family:Arial,sans-serif;font-size:7.5px;line-height:12.5px;color:#777;text-align:justify}
.card-btn{position:absolute;left:46px;top:196px;width:91px;height:20px;border:1.5px solid;font-size:8.5px;text-align:center;line-height:17px;letter-spacing:.5px;font-weight:500}
.sermons .card-arch,.sermons .card-head{background:var(--blue)}
.sermons .card-btn{color:var(--blue);border-color:var(--blue)}
.events .card-arch,.events .card-head{background:var(--red)}
.events .card-btn{color:var(--red);border-color:var(--red)}
.weddings .card-arch,.weddings .card-head{background:var(--gold)}
.weddings .card-btn{color:var(--gold);border-color:var(--gold)}

.rule{left:31px;width:558px;height:2px;background:#cfcfcf}
.message{left:37px;top:1064px;width:560px;font-size:15.5px;letter-spacing:1.4px;line-height:24.7px;color:#222}
.message p{margin-bottom:24.5px}

/* blog */
.blog-title{left:0;top:1473px;width:612px;text-align:center;font-family:'Tinos',serif;font-weight:700;font-size:29px;color:#222;letter-spacing:.3px}
.blog-sub{left:0;top:1525px;width:612px;text-align:center;font-size:12.5px;line-height:19px;color:#444;letter-spacing:.4px}
.post{background:#fff;box-shadow:0 1px 4px rgba(0,0,0,.3)}
.post-photo{position:absolute}
.tag{position:absolute;height:14px;background:var(--red);color:#fff;font-size:6.5px;line-height:14px;padding:0 8px;border-radius:0 7px 7px 0}
.post-title{position:absolute;font-family:'Tinos',serif;font-size:9.5px;color:#222;line-height:14px}
.post-text{position:absolute;font-size:6px;line-height:8.5px;color:#888}
.post-lead .post-text{font-size:8.5px;line-height:12.5px}
.read{position:absolute;color:var(--red);font-size:6px;font-weight:500}
.post-lead .read{font-size:8.5px}
.more-btn{left:453px;top:1923px;width:100px;height:24px;background:var(--navy);color:#fff;font-size:10px;letter-spacing:3px;text-align:center;line-height:24px;font-weight:500}

/* side panels */
.panel{left:652px;width:343px;background:var(--panel);border:1px solid var(--panel-line);border-radius:22px}
.panel-title{position:absolute;left:0;width:100%;text-align:center;font-family:'Tinos',serif;font-weight:700;font-size:24px;color:var(--navy);letter-spacing:.5px}
.contact-lines{position:absolute;left:21px;top:96px;font-size:16px;line-height:18.5px;color:var(--navy)}
.contact-lines p{margin-bottom:26px}
.event-head{position:absolute;left:20px;top:88px;font-size:19.5px;color:var(--navy);letter-spacing:.4px}
.event-date{position:absolute;left:126px;font-size:19px;color:var(--navy)}
.event-time{position:absolute;left:127px;font-size:15.5px;color:var(--navy)}
.event-name{position:absolute;left:24px;font-size:15.5px;color:var(--navy);letter-spacing:.3px}
.find-btn{position:absolute;left:24px;width:110px;height:21px;background:var(--navy);color:#fff;font-size:13px;text-align:center;line-height:21px}
.cal{position:absolute;left:21px}

.partner{left:677px;top:1752px;width:300px;height:76px}
.partner-dot{position:absolute;left:0;top:8px;width:70px;height:70px;border-radius:50%;background:var(--navy)}
.partner-name{position:absolute;left:82px;top:20px;font-size:17px;font-weight:600;color:var(--navy);line-height:23px;white-space:nowrap}

/* give */
.give{left:0;top:1986px;width:1019px;height:254px;background:linear-gradient(180deg,#4b5360 0%,#3b3d40 55%,#2e2b29 100%)}
.give-box{left:283px;top:2008px;width:452px;height:210px;background:rgba(16,44,76,.93);color:#fff;text-align:center}
.give-title{position:absolute;left:0;width:100%;top:20px;font-size:30px;font-weight:600;letter-spacing:7px}
.give-line{position:absolute;left:0;width:100%;font-family:'Roboto',sans-serif;font-size:14px}
.gift-btn{position:absolute;left:149px;top:160px;width:154px;height:32px;border:1.5px solid #fff;font-size:16px;line-height:29px;letter-spacing:.5px}

/* footer */
.footer{left:0;top:2240px;width:1019px;height:85px;background:var(--navy);color:#fff}
.foot-nav{position:absolute;top:25px;font-size:12px;letter-spacing:.5px;white-space:nowrap}
.foot-sep{position:absolute;top:24px;width:1px;height:15px;background:#fff}
.foot-rule{position:absolute;left:210px;top:51px;width:600px;height:1px;background:#aab6c5}
.copyright{position:absolute;left:0;width:100%;top:63px;text-align:center;font-size:10px;letter-spacing:.6px}
</style>
</head>
<body>
<div class="page">

  <!-- header -->
  <div class="abs hero" role="img" aria-label="Group photo of the congregation gathered in front of a mural wall"></div>
  <div class="abs hero-shade"></div>
  <div class="abs topbar"></div>

  <div class="abs social" style="left:174px"></div>
  <div class="abs social" style="left:210px">
    <svg width="10" height="10" viewBox="0 0 10 10"><path d="M2 1 L4 1 L4.6 3 L3.5 3.8 Q4.5 5.8 6.2 6.5 L7 5.4 L9 6 L9 8 Q5 9 2.2 5.5 Q1 3.5 2 1Z" fill="#fff"/></svg>
  </div>
  <div class="abs social" style="left:246px">
    <svg width="10" height="10" viewBox="0 0 10 10"><rect x="1" y="2.5" width="8" height="5.5" fill="none" stroke="#fff" stroke-width="1"/><path d="M1 2.5 L5 5.5 L9 2.5" fill="none" stroke="#fff" stroke-width="1"/></svg>
  </div>
  <div class="abs contact-btn">Contact</div>

  <nav class="abs nav">
    <span class="active" style="left:40px">HOME</span>
    <span class="sep" style="left:92px"></span>
    <span style="left:106px">SERMONS</span>
    <span class="sep" style="left:172px"></span>
    <span style="left:182px">ABOUT US &nbsp;&nbsp;⌄</span>
    <span style="left:427px">CHURCH LIFE &nbsp;&nbsp;&nbsp;⌄</span>
    <span class="sep" style="left:533px"></span>
    <span style="left:541px">NEWS &nbsp;⌄</span>
    <span class="sep" style="left:590px"></span>
    <span style="left:600px">WEDDINGS</span>
  </nav>

  <svg class="abs logo-tab" viewBox="0 0 116 122"><path d="M0 0 H116 V100 L58 122 L0 100 Z" fill="#fff"/></svg>
  <div class="abs logo-top">COVENANT<br>FELLOWSHIP</div>
  <div class="abs logo-name">ELMRIDGE</div>
  <div class="abs logo-sub">COVENANT FELLOWSHIP</div>

  <div class="abs quote">“Celebrate and Share the Love of God.<br>Together we want to be a place Where Love Comes to Life”</div>
  <div class="abs schedule-btn">SCHEDULE</div>

  <section class="abs band">
    <div class="band-title">SERVICE SCHEDULE</div>
    <div class="band-times">SATURDAY 6PM | SUNDAY 8.30AM &amp; 10.20AM</div>
  </section>

  <!-- feature cards -->
  <article class="abs card sermons" style="left:26px">
    <div class="card-arch"></div>
    <div class="card-body">
      <div class="card-head">Sermons</div>
      <div class="card-photo" role="img" aria-label="Headphones resting beside a phone" style="background:linear-gradient(135deg,#e9b8a8,#8fb3c4)"></div>
      <p class="card-text"><b>Lorem Ipsum</b> text is simply placeholder (or ‘dummy’) text that is frequently used by designers, publishers, printers and</p>
      <div class="card-btn">Learn More</div>
    </div>
  </article>
  <article class="abs card events" style="left:225px">
    <div class="card-arch"></div>
    <div class="card-body">
      <div class="card-head">Events</div>
      <div class="card-photo" role="img" aria-label="Crowd at a worship event on stage" style="background:linear-gradient(135deg,#3a2a4a,#7a3a5a)"></div>
      <p class="card-text"><b>Lorem Ipsum</b> text is simply placeholder (or ‘dummy’) text that is frequently used by designers, publishers, printers and</p>
      <div class="card-btn">Learn More</div>
    </div>
  </article>
  <article class="abs card weddings" style="left:425px">
    <div class="card-arch"></div>
    <div class="card-body">
      <div class="card-head">Weddings</div>
      <div class="card-photo" role="img" aria-label="Wedding couple at the church altar" style="background:linear-gradient(135deg,#c9a86a,#7a5a2e)"></div>
      <p class="card-text"><b>Lorem Ipsum</b> text is simply placeholder (or ‘dummy’) text that is frequently used by designers, publishers, printers and</p>
      <div class="card-btn">Learn More</div>
    </div>
  </article>

  <div class="abs rule" style="top:1021px"></div>

  <div class="abs message">
    <p>CHRISTMAS WORSHIP TIMES – click here</p>
    <p>There have been changes to our usual worship format –<br>you can &nbsp;Join us in person or worship online</p>
    <p>You watch this week’s sermon on our website<br>https://watch.elmridgechurch.org.au/live</p>
    <p>“I have told you these things, so that in me you may have peace. In this world you will have trouble. But take heart! I have overcome the world.” (John 16:33)</p>
    <p>In Christ our hope and peace,<br>Pastor Daniel Hart and Pastor Simon Reid</p>
  </div>

  <div class="abs rule" style="top:1447px"></div>

  <!-- blog -->
  <h2 class="abs blog-title">LATEST FROM BLOG</h2>
  <p class="abs blog-sub">Lorem ipsum dolor sit amet, consectetur adipiscing elit.<br>Cras at urna mollis neque efficitur feugiat.</p>

  <article class="abs post post-lead" style="left:51px;top:1596px;width:220px;height:304px">
    <div class="post-photo" role="img" aria-label="Youth camp poster in deep purple and red" style="left:0;top:0;width:220px;height:151px;background:radial-gradient(circle at 50% 75%,#9a2a3e,#3a1c4a 70%)"></div>
    <div class="tag" style="left:0;top:160px">OCTOBER 02, 2020</div>
    <div class="post-title" style="left:10px;top:182px;width:205px">CFYWA (Covenant Fellowship Youth of Western Australia) JAN CAMP 2021</div>
    <div class="post-text" style="left:10px;top:220px;width:200px">Lorem ipsum dolor sit amet, consectetur adipiscing elit. Cras at urna mollis neque efficitur feugiat. Orci varius natoque penatibus et magnis dis parturient montes, nascetur ridiculus mus.</div>
    <div class="read" style="left:136px;top:284px">READ MORE ›</div>
  </article>

  <article class="abs post" style="left:282px;top:1596px;width:277px;height:145px">
    <div class="post-photo" role="img" aria-label="Congregation gathered for Sunday worship" style="left:0;top:0;width:116px;height:145px;background:linear-gradient(160deg,#4c4a4a,#2f2d2e)"></div>
    <div class="tag" style="left:116px;top:16px">OCTOBER 16, 2020</div>
    <div class="post-title" style="left:125px;top:42px">Sunday morning worship</div>
    <div class="post-text" style="left:125px;top:70px;width:142px">Lorem ipsum dolor sit amet, consectetur adipiscing elit. Cras at urna mollis neque efficitur feugiat. Orci varius natoque penatibus et magnis dis parturient montes, nascetur ridiculus mus.</div>
    <div class="read" style="left:222px;top:125px">READ MORE ›</div>
  </article>

  <article class="abs post" style="left:282px;top:1752px;width:277px;height:148px">
    <div class="post-photo" role="img" aria-label="Church members standing beside the baptismal font" style="left:0;top:0;width:116px;height:148px;background:linear-gradient(160deg,#9a8a78,#5a4a3e)"></div>
    <div class="tag" style="left:116px;top:16px">OCTOBER 29, 2020</div>
    <div class="post-title" style="left:120px;top:41px">Saturday night worship</div>
    <div class="post-text" style="left:125px;top:78px;width:142px">Lorem ipsum dolor sit amet, consectetur adipiscing elit. Cras at urna mollis neque efficitur feugiat. Orci varius natoque penatibus et magnis dis parturient montes, nascetur ridiculus mus.</div>
    <div class="read" style="left:222px;top:132px">READ MORE ›</div>
  </article>

  <div class="abs more-btn">MORE</div>

  <!-- contact panel -->
  <aside class="abs panel" style="top:727px;height:383px">
    <h3 class="panel-title" style="top:34px">CONTACT DETAILS</h3>
    <div class="contact-lines">
      <p>Address :<br>42 Carrow Lane<br>Eastvale, WA 6100</p>
      <p>Office Hours :<br>Tuesday, Thursday &amp; Friday: 9am-4pm</p>
      <p>Phone : 08 9400 1234<br>Email : hello@elmridgechurch.org.au</p>
      <p>Donations:<br>Elmridge Covenant Fellowship<br>BSB: 062 118 Account: 1029 55731</p>
    </div>
  </aside>

  <!-- events panel -->
  <aside class="abs panel" style="top:1153px;height:515px">
    <h3 class="panel-title" style="top:28px">UPCOMING EVENT</h3>
    <div class="event-head">CHRISTMAS WORSHIP TIMES</div>

    <svg class="cal" style="top:140px" width="92" height="72" viewBox="0 0 92 72">
      <rect x="2" y="6" width="80" height="62" fill="none" stroke="#153e66" stroke-width="4"/>
      <line x1="2" y1="18" x2="82" y2="18" stroke="#153e66" stroke-width="4"/>
      <g stroke="#153e66" stroke-width="4"><line x1="14" y1="0" x2="14" y2="12"/><line x1="30" y1="0" x2="30" y2="12"/><line x1="46" y1="0" x2="46" y2="12"/><line x1="62" y1="0" x2="62" y2="12"/></g>
      <g fill="#153e66"><rect x="10" y="28" width="10" height="4"/><rect x="26" y="28" width="10" height="4"/><rect x="42" y="28" width="10" height="4"/><rect x="58" y="28" width="10" height="4"/><rect x="10" y="40" width="10" height="4"/><rect x="26" y="40" width="10" height="4"/><rect x="42" y="40" width="10" height="4"/><rect x="10" y="52" width="10" height="4"/><rect x="26" y="52" width="10" height="4"/><rect x="42" y="52" width="10" height="4"/></g>
      <circle cx="74" cy="56" r="15" fill="#f2f2f2" stroke="#153e66" stroke-width="4"/>
      <path d="M74 47 V57 H82" fill="none" stroke="#153e66" stroke-width="3"/>
    </svg>
    <div class="event-date" style="top:144px">Dec, 24 2020</div>
    <div class="event-time" style="top:169px">1 PM - 4 PM</div>
    <div class="event-name" style="top:227px">German Service</div>
    <div class="find-btn" style="top:259px">Fine out more</div>

    <svg class="cal" style="top:331px" width="92" height="72" viewBox="0 0 92 72">
      <rect x="2" y="6" width="80" height="62" fill="none" stroke="#153e66" stroke-width="4"/>
      <line x1="2" y1="18" x2="82" y2="18" stroke="#153e66" stroke-width="4"/>
      <g stroke="#153e66" stroke-width="4"><line x1="14" y1="0" x2="14" y2="12"/><line x1="30" y1="0" x2="30" y2="12"/><line x1="46" y1="0" x2="46" y2="12"/><line x1="62" y1="0" x2="62" y2="12"/></g>
      <g fill="#153e66"><rect x="10" y="28" width="10" height="4"/><rect x="26" y="28" width="10" height="4"/><rect x="42" y="28" width="10" height="4"/><rect x="58" y="28" width="10" height="4"/><rect x="10" y="40" width="10" height="4"/><rect x="26" y="40" width="10" height="4"/><rect x="42" y="40" width="10" height="4"/><rect x="10" y="52" width="10" height="4"/><rect x="26" y="52" width="10" height="4"/><rect x="42" y="52" width="10" height="4"/></g>
      <circle cx="74" cy="56" r="15" fill="#f2f2f2" stroke="#153e66" stroke-width="4"/>
      <path d="M74 47 V57 H82" fill="none" stroke="#153e66" stroke-width="3"/>
    </svg>
    <div class="event-date" style="top:335px">Dec, 25 2020</div>
    <div class="event-time" style="top:359px">8.30 AM - 10.00 AM</div>
    <div class="event-name" style="top:417px">Worship with HC (Organ)</div>
    <div class="find-btn" style="top:450px">Fine out more</div>
  </aside>

  <div class="abs partner">
    <div class="partner-dot"></div>
    <div class="partner-name">COVENANT FELLOWSHIP<br>of Australia</div>
  </div>

  <!-- give -->
  <section class="abs give" role="img" aria-label="Evening street view of the church building and neighbouring houses"></section>
  <div class="abs give-box">
    <div class="give-title">GIVE TODAY</div>
    <div class="give-line" style="top:80px;font-weight:700">Elmridge Covenant Fellowship</div>
    <div class="give-line" style="top:106px">BSB : 062 118</div>
    <div class="give-line" style="top:132px">Account : 1029 55731</div>
    <div class="gift-btn">MAKE A GIFT</div>
  </div>

  <!-- footer -->
  <footer class="abs footer">
    <span class="foot-nav" style="left:168px;font-weight:600">HOME</span>
    <span class="foot-sep" style="left:233px"></span>
    <span class="foot-nav" style="left:249px">SERMONS</span>
    <span class="foot-sep" style="left:340px"></span>
    <span class="foot-nav" style="left:355px">ABOUT US &nbsp;&nbsp;⌄</span>
    <span class="foot-sep" style="left:455px"></span>
    <span class="foot-nav" style="left:467px">CHURCH LIFE &nbsp;&nbsp;⌄</span>
    <span class="foot-sep" style="left:592px"></span>
    <span class="foot-nav" style="left:603px">NEWS &nbsp;⌄</span>
    <span class="foot-sep" style="left:671px"></span>
    <span class="foot-nav" style="left:685px">WEDDINGS</span>
    <span class="foot-sep" style="left:771px"></span>
    <span class="foot-nav" style="left:786px">CONTACTS</span>
    <div class="foot-rule"></div>
    <div class="copyright">©2020 &nbsp;| &nbsp;https://elmridgechurch.org.au/ &nbsp;| &nbsp;Allright &nbsp;Reserved</div>
  </footer>
</div>
</body>
</html>
```